Business Card Design for Translation Company - Rush

Rush job for a business card designing for a company doing international translations, several Asian and western languages. Already have a logo design (see attached) to use as the basis of the business card design. For the card, we also need the full company name, address, email, and phone number. In addition, my name as I will be the one handing out the cards.

For the logo design, we think the white background would be best. But we will consider using the dark background if you have a great idea for it.

The attached jpeg design has just been approved, but the designer has not yet finalized the file. When we select our final applicant, we will send the finalized file. (Nothing changes except the quality of the data.)

The phone number may change and if so, we will send the new one when we select our applicant.

We must complete the entire process and have a design ready to go to print no later than 01:00 am August 3, New York (East Coast) time.

We look forward to your participation in the project,
Dale

Target Market(s)

Translation clients worldwide.

Industry/Entity Type

Business

Contact Information for Business Card

Company details:

Korvanta Translations International, Ltd.

#207-2836 Wexholm Avenue, Victoria, BC, Canada V9T3K2

jquell@korvantatranslations.example

+1-888-604-7321

Font styles to use
Sans Serif

Requirements
Must have
• Company name, address, email and phone number.
• Also my name:
• Gordon R. Quell
• Director
Nice to have
• Not a demand, but please consider creatively using the horizontal bar.
Should not have
• Cluttered of jumbled appearance.

```html
<!DOCTYPE html>
<html lang="en">
<head>
<meta charset="utf-8">
<title>Korvanta Translations – Business Card</title>
<link href="https://fonts.googleapis.com/css2?family=Montserrat:wght@400;600;700&family=Open+Sans:wght@400;600&display=swap" rel="stylesheet">
<style>
  :root {
    --orange: #ef7a22;
    --ink: #2b2b2b;
    --grey: #555555;
    --paper: #ffffff;
    --black: #161616;
    --charcoal: #3a3a3a;
    --backdrop: #e9e6e1;
  }
  * { box-sizing: border-box; margin: 0; padding: 0; }
  html, body {
    width: 1200px; height: 1024px; overflow: hidden;
    background: var(--backdrop);
    font-family: "Open Sans", Arial, sans-serif;
  }
  .canvas {
    position: relative; width: 1200px; height: 1024px;
  }
  .card {
    position: absolute; width: 630px; height: 360px;
    box-shadow: 0 10px 28px rgba(0,0,0,.22);
    overflow: hidden;
  }
  /* Front */
  .card-front { left: 90px; top: 90px; background: var(--paper); }
  .card-front .edge-band {
    position: absolute; left: 0; right: 0; bottom: 0; height: 22px;
    background: var(--orange);
  }
  .brand {
    display: flex; align-items: center; gap: 12px;
    font-family: "Montserrat", Arial, sans-serif;
    font-weight: 600; letter-spacing: 3px; text-transform: uppercase;
    color: var(--ink);
  }
  .brand-dot {
    width: 22px; height: 22px; border-radius: 50%;
    background: var(--orange); flex: none;
  }
  .card-front .brand { position: absolute; left: 48px; top: 60px; font-size: 17px; }
  .brand-rule {
    position: absolute; height: 2px; background: var(--orange);
  }
  .card-front .brand-rule { left: 48px; top: 100px; width: 300px; }
  .holder { position: absolute; left: 48px; bottom: 70px; }
  .holder-rule { width: 150px; height: 2px; background: var(--orange); margin-bottom: 14px; }
  .holder-name {
    font-family: "Montserrat", Arial, sans-serif; font-weight: 700;
    font-size: 16px; letter-spacing: 1px; text-transform: uppercase; color: var(--ink);
  }
  .holder-title { font-size: 13px; color: var(--orange); margin-top: 2px; }
  .contact {
    position: absolute; left: 330px; top: 150px; width: 280px;
    font-size: 11.5px; line-height: 1.55; color: var(--grey);
  }
  .contact .label { color: var(--orange); font-weight: 600; }
  .contact .address { margin-top: 14px; }
  /* Back */
  .card-back {
    left: 480px; top: 560px;
    background: linear-gradient(160deg, var(--charcoal) 0%, var(--black) 60%);
  }
  .card-back .brand {
    position: absolute; left: 60px; top: 190px; font-size: 22px; color: var(--paper);
  }
  .card-back .brand-dot { width: 28px; height: 28px; }
  .card-back .brand-rule { left: 60px; top: 240px; width: 420px; }
  .web {
    position: absolute; left: 60px; top: 260px;
    font-size: 14px; color: var(--orange); letter-spacing: .3px;
  }
</style>
</head>
<body>
<main class="canvas">
  <section class="card card-front" aria-label="Business card front">
    <div class="brand"><span class="brand-dot"></span>Korvanta Translations</div>
    <div class="brand-rule"></div>
    <div class="holder">
      <div class="holder-rule"></div>
      <div class="holder-name">Gordon R. Quell</div>
      <div class="holder-title">Director</div>
    </div>
    <div class="contact">
      <div><span class="label">P:</span> +1-888-604-7321</div>
      <div><span class="label">E:</span> jquell@korvantatranslations.example</div>
      <div class="address">Korvanta Translations International, Ltd.<br>#207-2836 Wexholm Avenue, Victoria, BC,<br>Canada V9T3K2</div>
    </div>
    <div class="edge-band"></div>
  </section>

  <section class="card card-back" aria-label="Business card back">
    <div class="brand"><span class="brand-dot"></span>Korvanta Translations</div>
    <div class="brand-rule"></div>
    <div class="web">www.korvantatranslations.example</div>
  </section>
</main>
</body>
</html>
```